Modern, clean and professional Wordpress design for a safety training company!

We are currently in the process of creating a new website for our business. We have hired a website developer and the main structure of our new Wordpress site is complete. We now need an overall design plan for the site. We need a very clean, professional and easy to follow website. Most of our website visitors only spend about 30-45 secs on our sites "shopping " so it is imperative that we have a strong Home Page.
Our company specializes in CPR and First Aid Certification Classes to businesses and individuals throughout Northern California. We provide these certifications two ways: ONSITE-We come to you, and HOSTED-we offer weekly classes at our 2 locations.
Our design needs to use the general green and blue colors of our logo. But we also like white.
The final design MUST communicate a legitimate, trustworthy and professional business. Our industry is VERY competitive and we need to STAND OUT.
Currently, the NEW website that we need a new design for is www.LifelineDrillWorks.com
Our old website is www.RescuePrepValleyHub.com and we really do like the design of this website, but we just needed a Wordpress site for SEO purposes.
These are 3 websites that we really:
http://morvaliontech.com/
http://www.tralbex.com/
https://www.plivant.com/
I have attached our Logo and other images if you need to use them but looking at the current two sites will be you best help.
Target Market(s)
1) Large businesses and industries that are looking for a company to provide ONSITE safety training classes at their office or place of work.
2) Individuals that need certifications for their jobs and other needs. These individuals are looking for a legitimate, trustworthy and professional environment to complete their training class.

```html
<!DOCTYPE html>
<html lang="en">
<head>
<meta charset="utf-8">
<title>Valleycrest Safety Institute</title>
<link href="https://fonts.googleapis.com/css2?family=Lato:ital,wght@0,300;0,400;0,700;1,400&display=swap" rel="stylesheet">
<style>
:root{
  --green:#8dc21f;
  --green-dark:#6f9c14;
  --title-green:#8cbf26;
  --blue:#1d3f95;
  --navy:#163a8c;
  --navy-deep:#0f2b6e;
  --text:#222;
  --line:#e2e2e2;
  --review-bg:#d4deb0;
  --white:#fff;
}
*{margin:0;padding:0;box-sizing:border-box}
html,body{width:720px;height:1200px;overflow:hidden;background:var(--white)}
body{position:relative;font-family:"Lato",sans-serif;color:var(--text)}
.abs{position:absolute}
.top-strip{left:0;top:0;width:720px;height:4px;background:var(--green)}
.hero-photo{left:0;top:4px;width:720px;height:360px;
  background:
    radial-gradient(ellipse 220px 140px at 180px 120px,rgba(120,160,190,.45),transparent 70%),
    radial-gradient(ellipse 260px 120px at 520px 300px,rgba(150,90,70,.45),transparent 70%),
    radial-gradient(ellipse 200px 90px at 110px 320px,rgba(200,170,60,.35),transparent 70%),
    linear-gradient(180deg,#eef2f5 0%,#d9e2e8 28%,#b9aa9a 52%,#8a6c58 75%,#4a3a30 100%)}
.brand{left:36px;top:18px;width:150px;font-weight:700;color:var(--blue);font-size:15px;line-height:1.15;letter-spacing:.3px}
.brand-mark{display:inline-block;width:16px;height:16px;border-radius:50%;background:var(--green);vertical-align:middle;margin-right:6px}
.contact{top:28px;font-size:8px;color:#333;display:flex;align-items:center;gap:4px}
.nav{left:202px;top:58px;width:482px;height:32px;background:var(--blue);display:flex;align-items:center;justify-content:space-around;padding:0 10px}
.nav a{color:var(--white);font-size:8px;text-decoration:none;letter-spacing:.2px}
.arrow{top:170px;width:22px;height:28px;background:#3a3a3a;display:flex;align-items:center;justify-content:center}
.hero-caption{left:0;width:720px;top:253px;text-align:center;color:var(--white);font-size:18px;font-weight:400}
.hero-caption span{background:rgba(90,110,60,.35);padding:0 6px}
.btn-green{background:var(--green);color:var(--white);display:flex;align-items:center;justify-content:center;border-bottom:2px solid var(--green-dark)}
.hero-btn{left:310px;top:287px;width:100px;height:28px;font-size:13px}
.dots{left:688px;top:296px;display:flex;gap:4px}
.dots i{width:5px;height:5px;border-radius:50%;background:rgba(255,255,255,.7)}
.welcome{left:0;width:720px;top:376px;text-align:center;color:var(--title-green);font-size:17px;font-weight:400}
.intro{left:50px;width:620px;text-align:center;font-size:8.2px;line-height:13.5px;color:#222}
.learn{left:310px;top:478px;width:100px;height:27px;font-size:10px}
.mode{top:522px;height:45px;border:1px solid var(--line);overflow:hidden}
.mode .photo{position:absolute;inset:0}
.mode h3{position:absolute;font-size:17px;font-weight:400;line-height:1}
.mode p{position:absolute;font-size:9px;color:#444}
.card{top:575px;width:146px;height:183px;border:1px solid var(--line);text-align:center}
.card h4{margin-top:27px;font-size:16px;font-weight:400;color:var(--title-green)}
.card .price{margin-top:10px;font-size:13px}
.card .kind{margin-top:11px;font-size:13px}
.card .dur{margin-top:18px;font-size:13px;color:var(--title-green)}
.card .reg{margin:9px auto 0;width:102px;height:25px;font-size:9.5px}
.review{left:355px;top:576px;width:329px;height:182px;background:var(--review-bg);padding:8px 15px}
.review h5{font-size:13px;font-weight:400;color:#333}
.review .meta{margin-top:8px;font-size:8px;font-style:italic;line-height:13px;color:#333}
.review .quote{margin-top:8px;font-size:9.4px;line-height:13.5px;color:#333}
.review .stars{margin-top:9px;display:flex;gap:2px}
.badge{margin-top:10px;display:flex;align-items:center;gap:5px}
.badge .b1{width:38px;height:6px;background:#9aa27c;border-radius:1px}
.badge .b2{width:60px;height:16px;background:#3a4a6a;border-radius:2px}
.map{left:35px;top:766px;width:649px;height:256px;
  background:
    radial-gradient(ellipse 260px 140px at 480px 160px,rgba(255,255,255,.55),transparent 70%),
    radial-gradient(ellipse 200px 120px at 120px 200px,rgba(205,198,182,.6),transparent 70%),
    linear-gradient(135deg,#ebe7df,#ddd8cd 55%,#e7e3da)}
.map-panel{left:50px;top:785px;width:192px;height:140px;background:var(--white);box-shadow:0 1px 3px rgba(0,0,0,.25)}
.map-panel .search{height:20px;border-bottom:1px solid #ddd}
.map-panel .thumb{position:absolute;left:6px;top:76px;width:180px;height:36px;background:linear-gradient(90deg,#4e5a3c,#8f9a7a 50%,#6a6a64)}
.map-label{left:355px;top:867px;font-size:10px;color:#222}
.map-ctrl{left:658px;top:994px;width:14px;height:28px;background:var(--white);box-shadow:0 1px 2px rgba(0,0,0,.2)}
.big-btn{top:1035px;width:283px;height:44px;color:var(--white);font-size:14.5px;display:flex;align-items:center;justify-content:center;letter-spacing:.3px;
  background:linear-gradient(180deg,var(--navy) 0%,var(--navy-deep) 100%)}
.footer{left:0;top:1101px;width:720px;height:99px;background:var(--blue)}
.flinks{left:0;width:720px;top:1115px;display:flex;justify-content:center;gap:11px;font-size:8px;color:var(--white)}
.frule{left:36px;top:1137px;width:648px;height:1px;background:rgba(255,255,255,.15)}
.social{top:1146px;width:28px;height:28px;border-radius:50%;border:1px solid rgba(255,255,255,.6);background:rgba(255,255,255,.06)}
.copy{left:0;width:720px;top:1184px;text-align:center;font-size:6.5px;color:var(--white)}
</style>
</head>
<body>
<div class="abs top-strip"></div>
<div class="abs hero-photo" role="img" aria-label="Photo of an instructor teaching a classroom of seated students"></div>

<div class="abs brand"><span class="brand-mark"></span>Valleycrest Safety Institute</div>

<div class="abs contact" style="left:516px">
  <svg width="7" height="9" viewBox="0 0 7 9"><rect x="1" y="0.5" width="5" height="8" rx="1" fill="none" stroke="#333"/></svg>916-555-0172
</div>
<div class="abs contact" style="left:592px">
  <svg width="9" height="7" viewBox="0 0 9 7"><rect x="0.5" y="0.5" width="8" height="6" fill="none" stroke="#333"/><path d="M.5 .5 4.5 4 8.5 .5" fill="none" stroke="#333"/></svg>INFO@VALLEYCRESTCPR.COM
</div>

<nav class="abs nav">
  <a>HOME</a><a>CLASS CALENDER</a><a>CLASSES FOR GROUPS</a><a>CERTIFICATION CLASSES</a><a>ABOUT US</a><a>POLICIES</a>
</nav>

<div class="abs arrow" style="left:0"><svg width="6" height="10" viewBox="0 0 6 10"><path d="M5 1 1 5l4 4" stroke="#fff" fill="none" stroke-width="1.5"/></svg></div>
<div class="abs arrow" style="left:698px"><svg width="6" height="10" viewBox="0 0 6 10"><path d="M1 1l4 4-4 4" stroke="#fff" fill="none" stroke-width="1.5"/></svg></div>

<div class="abs hero-caption"><span>CPR+First Aid $59 Adult/Child/Infant 3 hours or less!</span></div>
<div class="abs btn-green hero-btn">Register Now</div>
<div class="abs dots"><i></i><i></i><i></i></div>

<h1 class="abs welcome">WELCOME TO VALLEYCREST SAFETY INSTITUTE!</h1>
<p class="abs intro" style="top:404px">Valleycrest Safety Institute is Northern California's leader in CPR, BLS, and Basic First Aid Certifications! Taught by experienced Firefighters, our classes are much shorter and provide common sense knowledge and skills to each student to help prepare them for actual emergencies.</p>
<p class="abs intro" style="top:444px">By using real life emergency responders, we have revolutionized the standard, boring CPR class by teaching students the need-to-know information and preparing them with facts and tips to help them in true life and death situations!</p>
<div class="abs btn-green learn">LEARN MORE</div>

<div class="abs mode" style="left:35px;width:302px">
  <div class="photo" role="img" aria-label="Photo of hands practising CPR on a training manikin" style="background:linear-gradient(90deg,#c9c6d8,#e4e2ea 55%,#f2f2f2)"></div>
  <h3 style="right:16px;top:6px;color:var(--title-green)">ONSITE</h3>
  <p style="right:16px;top:25px">We come to you</p>
</div>
<div class="abs mode" style="left:355px;width:329px">
  <div class="photo" role="img" aria-label="Photo of a training room with CPR posters" style="background:linear-gradient(90deg,#f1f1f1 35%,#c4ccd8 50%,#e8eaec 75%,#d9dcdf)"></div>
  <h3 style="left:11px;top:6px;color:var(--blue)">HOSTED</h3>
  <p style="left:12px;top:25px">We offer weekly classes</p>
</div>

<div class="abs card" style="left:36px">
  <h4>CPR</h4><div class="price">$39</div><div class="kind">Adult/Child/Infant</div><div class="dur">90 Minutes!</div>
  <div class="btn-green reg">Register Now</div>
</div>
<div class="abs card" style="left:192px">
  <h4>BLS</h4><div class="price">$49</div><div class="kind">Healthcare/Dental</div><div class="dur">90 Minutes!</div>
  <div class="btn-green reg">Register Now</div>
</div>

<div class="abs review">
  <h5>Review</h5>
  <div class="meta">Marcus- CA, United States<br>February 26, 2014</div>
  <p class="quote">The instructor was awesome! Spoke very well, loud, and direct to the point. Made everything clear and easy to understand. Best CPR class with actual professionals.</p>
  <div class="stars">
    <svg width="56" height="11" viewBox="0 0 56 11">
      <g stroke="#1d3f95" stroke-width=".8">
        <path d="M5 .5l1.3 2.9 3.2.3-2.4 2.1.7 3.1L5 7.3 2.2 8.9l.7-3.1L.5 3.7l3.2-.3z" fill="#1d3f95"/>
        <path transform="translate(11)" d="M5 .5l1.3 2.9 3.2.3-2.4 2.1.7 3.1L5 7.3 2.2 8.9l.7-3.1L.5 3.7l3.2-.3z" fill="#1d3f95"/>
        <path transform="translate(22)" d="M5 .5l1.3 2.9 3.2.3-2.4 2.1.7 3.1L5 7.3 2.2 8.9l.7-3.1L.5 3.7l3.2-.3z" fill="#1d3f95"/>
        <path transform="translate(33)" d="M5 .5l1.3 2.9 3.2.3-2.4 2.1.7 3.1L5 7.3 2.2 8.9l.7-3.1L.5 3.7l3.2-.3z" fill="none"/>
        <path transform="translate(44)" d="M5 .5l1.3 2.9 3.2.3-2.4 2.1.7 3.1L5 7.3 2.2 8.9l.7-3.1L.5 3.7l3.2-.3z" fill="none"/>
      </g>
    </svg>
  </div>
  <div class="badge"><div class="b1"></div><div class="b2"></div></div>
</div>

<div class="abs map" role="img" aria-label="Street map showing the training center location"></div>
<div class="abs map-panel" role="img" aria-label="Map info card with address search, directions and street view preview"><div class="search"></div><div class="thumb"></div></div>
<div class="abs map-ctrl"></div>
<div class="abs map-label">OUR LOCATION</div>
<svg class="abs" style="left:355px;top:891px" width="10" height="16" viewBox="0 0 10 16"><path d="M5 15C5 15 0 8 0 5a5 5 0 0 1 10 0c0 3-5 10-5 10z" fill="#d93a2b"/><circle cx="5" cy="5" r="1.8" fill="#8a1d12"/></svg>

<div class="abs big-btn" style="left:60px">REGISTER AND PAY ONLINE</div>
<div class="abs big-btn" style="left:378px">REGISTER ONLY AND PAY LATER</div>

<footer class="abs footer"></footer>
<div class="abs flinks">
  <span>Home</span><span>/</span><span>Class Calender</span><span>/</span><span>Certification Classes</span><span>/</span><span>Classes for Groups</span><span>/</span><span>About Us</span><span>/</span><span>Policies</span><span>/</span><span>Medesto</span><span>/</span><span>Manteca/Tracy</span><span>/</span><span>Livermore</span>
</div>
<div class="abs frule"></div>
<div class="abs social" style="left:304px"></div>
<div class="abs social" style="left:346px"></div>
<div class="abs social" style="left:388px"></div>
<div class="abs copy">© 2015.www.valleycrestcpr.com</div>
</body>
</html>
```